TL - business card

Tallow Partners is an insurance brokerage firm, inovative, proactive, vigorous, which aims to become the leader of the insurance brokers in Anfrica. We should like to get some designs which should be avoided also in Gray / Metallic for the Administration and Orange / Blue for the Managers (ike in the picture sent). The Blue / Green logo is not the correct one, but the source of the file. Please adjust the color accordingly for the business cards. 1 / Orange / Blue 2 / Gray / Metallic We want something classic but which is transmitted strenght, inovation, modernity and most of all, rapidity. We want something start-up like, very punchy and catching eye remaining profesional at the same time. Name: Dorian Whitlock Function: Managing Director Address: N ° 17/18 Rua Veloso - R / C 2B Direita - Bairro Mutamba - Luanda Tel: (+244) 947 582 316 Email: dorian.whitlock@tallow-p.example Website: www.tallow-p. example We want classic in the front and creative, colorfull at the back. The cards will be printed in relief, with very high quality of paper.
Insurance Broker
Colors
Designer to choose colors to be used in the design.

```html
<!DOCTYPE html>
<html lang="en">
<head>
<meta charset="utf-8">
<title>Tallow Partners – Business Card</title>
<link rel="stylesheet" href="https://fonts.googleapis.com/css2?family=Lato:wght@400;700&family=Roboto:wght@700&display=swap">
<style>
  :root {
    --bg: #d3d3d3;
    --paper: #ffffff;
    --blue: #0b7bc2;
    --red: #de2a26;
    --orange: #f59a5c;
    --orange-mid: #ea6a38;
    --ink: #555555;
  }
  * { box-sizing: border-box; margin: 0; padding: 0; }
  html, body { width: 1125px; height: 1200px; overflow: hidden; }
  body { background: var(--bg); position: relative; font-family: "Lato", sans-serif; }

  .card {
    position: absolute;
    left: 178px;
    width: 768px;
    height: 437px;
    overflow: hidden;
  }
  .card--front { top: 140px; background: var(--paper); }
  .card--back { top: 626px; background: var(--blue); }

  .brand-mark {
    position: absolute;
    border-radius: 50%;
  }
  .card--front .brand-mark {
    left: 552px; top: 43px; width: 100px; height: 100px;
    background: var(--orange-mid);
  }
  .brand-name {
    position: absolute;
    font-family: "Roboto", sans-serif;
    font-weight: 700;
    font-size: 28px;
    line-height: 1;
    letter-spacing: 0.5px;
    white-space: nowrap;
  }
  .card--front .brand-name { right: 32px; top: 150px; color: var(--blue); }

  .holder-name {
    position: absolute; left: 43px; top: 190px;
    font-family: "Roboto", sans-serif; font-weight: 700;
    font-size: 27px; letter-spacing: 1px; color: var(--blue);
  }
  .holder-role {
    position: absolute; left: 43px; top: 226px;
    font-size: 18px; color: var(--ink);
  }
  .divider {
    position: absolute; left: 43px; top: 275px; width: 693px; height: 1.5px;
    background: linear-gradient(90deg, var(--red), var(--orange));
  }

  .contact-list { position: absolute; left: 43px; top: 298px; list-style: none; }
  .contact-item {
    display: flex; align-items: center; height: 30px;
    font-size: 17.5px; color: var(--ink);
  }
  .contact-icon { width: 14px; height: 14px; margin-right: 12px; fill: var(--blue); flex: none; }

  .address {
    position: absolute; right: 32px; top: 336px; text-align: right;
    font-size: 17.5px; line-height: 23px; color: var(--ink);
  }

  .bands { position: absolute; left: 0; top: 0; width: 768px; height: 437px; }

  .card--back .brand-mark {
    left: 327px; top: 145px; width: 114px; height: 114px;
    background: #ffffff;
  }
  .card--back .brand-name {
    left: 0; right: 0; top: 266px; text-align: center;
    color: #ffffff; font-size: 30px;
  }
  .back-web {
    position: absolute; left: 0; right: 0; top: 384px; text-align: center;
    font-size: 17.5px; color: #ffffff;
  }
</style>
</head>
<body>
  <section class="card card--front">
    <div class="brand-mark"></div>
    <div class="brand-name">TALLOW PARTNERS</div>

    <h1 class="holder-name">Dorian Whitlock</h1>
    <p class="holder-role">Managing Director</p>
    <div class="divider"></div>

    <ul class="contact-list">
      <li class="contact-item">
        <svg class="contact-icon" viewBox="0 0 24 24"><path d="M6.6 10.8a15.1 15.1 0 0 0 6.6 6.6l2.2-2.2c.3-.3.7-.4 1-.2 1.1.4 2.3.6 3.6.6.6 0 1 .4 1 1V20c0 .6-.4 1-1 1A17 17 0 0 1 3 4c0-.6.4-1 1-1h3.5c.6 0 1 .4 1 1 0 1.3.2 2.5.6 3.6.1.3 0 .7-.2 1z"/></svg>
        (+244) 947 582 316
      </li>
      <li class="contact-item">
        <svg class="contact-icon" viewBox="0 0 24 24"><path d="M2 4h20v16H2zm2 2v.5l8 5.5 8-5.5V6zm0 3v9h16V9l-8 5.5z"/></svg>
        dorian.whitlock@tallow-p.example
      </li>
      <li class="contact-item">
        <svg class="contact-icon" viewBox="0 0 24 24"><circle cx="12" cy="12" r="10"/></svg>
        www.tallow-p. example
      </li>
    </ul>

    <p class="address">N ° 17/18 Rua Veloso - R / C 2B<br>Direita - Bairro Mutamba - Luanda</p>

    <svg class="bands" viewBox="0 0 768 437" aria-hidden="true">
      <defs>
        <linearGradient id="warm" x1="0" x2="1" y1="0" y2="0">
          <stop offset="0" stop-color="#de2a26"/>
          <stop offset="0.55" stop-color="#e8592f"/>
          <stop offset="1" stop-color="#f59a5c"/>
        </linearGradient>
      </defs>
      <path d="M0 405 H400 Q405 405 410 406 L405 414 H0 Z" fill="#0b7bc2"/>
      <path d="M0 422 H365 C400 422 415 415 445 405 C465 399 480 398 500 398 H768 V437 H0 Z" fill="url(#warm)"/>
    </svg>
  </section>

  <section class="card card--back">
    <div class="brand-mark"></div>
    <div class="brand-name">TALLOW PARTNERS</div>
    <p class="back-web">www.tallow-p. example</p>
  </section>
</body>
</html>
```